Tavenhurst Falcons FC Website

We are looking to develop a new website for Tavenhurst FC. Tavenhurst FC has now joined with Tavenhurst Falcons FC and we are looking at a website that can work for both clubs. Tavenhurst FC play in a local park football competition while tavenhurst Falcons are a Semi Professional team that plays in the Ostral Premier Series Competition. What we are after is two separate website off the one platform. I have attached both team logos for you to visualise. Also you can look at the existing tavenhurst website www.tavenhurstfc.net.au. We are looking for a huge improvement in the website and it will be imperative we have links to sponsors and the sponsors can get regular visuals. Weare looking to move this club forward and have a very professional website that can communicate clearly with the community.

Hi All,

Please remember that the website is to represent two clubs;
1. Tavenhurst Falcons FC (Competes in Semi Professional League)
2. Tavenhurst FC (Compete in KPWLT League which is a lower level)

Further to this the Tavenhurst Falcons FC page will require a player profile page which will show photos of each player and a little bio on each.

Thanks

Reason: Would like to spend more time review existing and new designs

```html
<!DOCTYPE html>
<html lang="en">
<head>
<meta charset="utf-8">
<title>Tavenhurst FC – Club Forms</title>
<link href="https://fonts.googleapis.com/css2?family=Roboto+Condensed:wght@400;700&family=Noto+Serif:ital,wght@0,400;1,400&family=Arimo:wght@400&display=swap" rel="stylesheet">
<style>
:root{
  --red:#e8231f;
  --red-dark:#d81b17;
  --red-deep:#b8120f;
  --black:#0d0d0d;
  --white:#ffffff;
  --panel:#f1f1f1;
  --tab-grey:#d9d9d9;
  --text:#222222;
  --muted:#555555;
  --footer-top:#ededed;
  --footer-bottom:#cfd8d6;
}
*{margin:0;padding:0;box-sizing:border-box}
html,body{width:750px;height:1200px;overflow:hidden;background:var(--white)}
.page{position:relative;width:750px;height:1200px;overflow:hidden;font-family:"Arimo",Arial,sans-serif;color:var(--text)}

/* top bar */
.topbar{position:absolute;left:0;top:0;width:750px;height:32px;background:var(--red-dark);font-family:"Roboto Condensed",sans-serif;font-weight:700;font-size:10px;color:var(--white);text-transform:uppercase}
.topbar .link{position:absolute;top:10px}
.topbar .link.join{left:94px}
.topbar .link.tickets{left:208px}
.topbar .divider{position:absolute;left:183px;top:0;width:1px;height:32px;background:rgba(255,255,255,.25)}
.topbar .follow{position:absolute;left:456px;top:10px}
.social{position:absolute;left:527px;top:9px;display:flex;gap:9px}
.social span{display:block;width:14px;height:14px;background:var(--white);border-radius:2px}

/* nav */
.nav{position:absolute;left:0;top:32px;width:750px;height:66px;background:var(--red);font-family:"Roboto Condensed",sans-serif;font-weight:700;font-size:16px;color:var(--white)}
.nav .item{position:absolute;top:23px}
.nav .item.active{top:0;height:66px;background:var(--red-deep);padding:23px 9px 0}
.brand{position:absolute;left:325px;top:0;width:99px;height:110px;background:var(--white);z-index:3;display:flex;flex-direction:column;align-items:center;justify-content:center;gap:8px;box-shadow:0 1px 3px rgba(0,0,0,.25)}
.brand .mark{width:22px;height:22px;border-radius:50%;background:var(--red)}
.brand .name{font-family:"Roboto Condensed",sans-serif;font-weight:700;font-size:12px;color:var(--red);text-align:center;line-height:1.15;text-transform:uppercase}

/* hero */
.hero{position:absolute;left:0;top:98px;width:750px;height:392px;background:radial-gradient(ellipse at 38% 35%,#6a2a22 0%,#3a1c18 35%,#1b1414 70%),#1b1414}
.hero-rule{position:absolute;left:0;top:490px;width:750px;height:4px;background:var(--red)}
.subnav{position:absolute;left:0;top:121px;z-index:2}
.subnav .tab{position:absolute;left:0;height:36px;padding:0 10px;font-family:"Noto Serif",serif;font-style:italic;font-size:15px;line-height:34px;white-space:nowrap}
.subnav .tab.light{background:var(--tab-grey);color:var(--black);border:2px solid #9a9a9a}
.subnav .tab.red{background:var(--red);color:var(--white);border:2px solid #a5110e}
.hero-icon{position:absolute;left:341px;top:225px}
.hero-title{position:absolute;left:0;top:294px;width:750px;text-align:center;font-family:"Noto Serif",serif;font-style:italic;font-size:31px;color:var(--white)}

/* content */
.content{position:absolute;left:0;top:494px;width:750px;height:514px;background:var(--panel)}
.intro-band{position:absolute;left:0;top:0;width:750px;height:68px;background:var(--white);border-left:1px solid #ddd;border-right:1px solid #ddd}
.dots{position:absolute;left:0;top:20px;width:750px;text-align:center;font-size:18px;letter-spacing:3px;color:var(--black)}
.section-rule{position:absolute;top:68px;height:1px;background:#cfcfcf}
.section-title{position:absolute;left:0;top:59px;width:750px;text-align:center;font-family:"Noto Serif",serif;font-style:italic;font-size:17px;color:var(--black);letter-spacing:.5px}
.section-title span{background:var(--panel);padding:0 14px}
.intro-text{position:absolute;left:36px;top:108px;width:678px;text-align:center;font-size:11.4px;line-height:12.4px;color:var(--text)}

.form-btn{position:absolute;width:210px;height:36px;border-radius:4px;font-family:"Noto Serif",serif;font-style:italic;font-size:15.5px;line-height:36px;padding-left:12px;white-space:nowrap;overflow:visible}
.form-btn.red{background:var(--red);color:var(--white);text-align:center;padding:0}
.form-btn.black{background:var(--black);color:var(--white);font-size:14px}
.form-btn.small{font-size:14px;padding:0 0 0 6px;text-align:left}
.badge{position:absolute;width:42px;height:42px;border-radius:50%;display:flex;align-items:center;justify-content:center;font-family:"Noto Serif",serif;font-size:22px;color:var(--white)}
.badge::after{content:"";position:absolute;inset:3px;border-radius:50%;border:1.5px dashed rgba(255,255,255,.9)}
.badge.red{background:var(--red)}
.badge.black{background:var(--black)}

/* footer */
.footer-rule{position:absolute;left:0;top:1008px;width:750px;height:5px;background:var(--red)}
.footer{position:absolute;left:0;top:1013px;width:750px;height:173px;background:linear-gradient(var(--footer-top) 0%,#e6e6e6 55%,var(--footer-bottom) 100%)}
.footer-col{position:absolute;top:0}
.footer-col h3{position:absolute;font-family:"Roboto Condensed",sans-serif;font-weight:400;font-size:19px;color:var(--black);top:34px;white-space:nowrap;text-transform:uppercase}
.footer-col .underline{position:absolute;top:63px;height:1px;background:#9a9a9a}
.footer-col ul{list-style:none;position:absolute;top:77px;font-family:"Roboto Condensed",sans-serif;font-size:14px;line-height:19px;color:#444}
.fixture-row{display:flex;justify-content:space-between;width:281px}
.footer-icon{position:absolute}
.copyright{position:absolute;left:0;top:1186px;width:750px;height:14px;background:var(--red);color:var(--white);font-size:8.5px;line-height:14px;padding-left:95px}
</style>
</head>
<body>
<div class="page">

  <header class="topbar">
    <span class="link join">Join us now ▸</span>
    <span class="divider"></span>
    <span class="link tickets">Get your tickets ▸</span>
    <span class="follow">Follow us :</span>
    <div class="social" aria-label="Social links">
      <span></span><span></span><span></span><span></span><span></span>
    </div>
  </header>

  <nav class="nav">
    <span class="item" style="left:26px">Home</span>
    <span class="item" style="left:92px">Photo Gallery</span>
    <span class="item" style="left:199px">Fixture &amp; Results</span>
    <span class="item" style="left:439px">News</span>
    <span class="item" style="left:498px">Sponsor</span>
    <span class="item active" style="left:553px">Club</span>
    <span class="item" style="left:619px">Contact Us</span>
    <svg class="item" style="left:701px;top:20px" width="20" height="20" viewBox="0 0 20 20" aria-label="Search">
      <circle cx="8" cy="8" r="5.5" fill="none" stroke="#fff" stroke-width="2.4"/>
      <line x1="12" y1="12" x2="17" y2="17" stroke="#fff" stroke-width="2.6" stroke-linecap="round"/>
    </svg>
  </nav>

  <div class="brand">
    <span class="mark"></span>
    <span class="name">Tavenhurst<br>Falcons FC</span>
  </div>

  <section class="hero" role="img" aria-label="Action photo of club players celebrating on the pitch in red kits"></section>
  <div class="hero-rule"></div>

  <div class="subnav">
    <span class="tab light" style="top:0">Tavenhurst FC History</span>
    <span class="tab red" style="top:49px">Committee Members</span>
    <span class="tab light" style="top:99px">Club Awards</span>
    <span class="tab red" style="top:148px">Club Forms</span>
  </div>

  <svg class="hero-icon" width="68" height="68" viewBox="0 0 68 68" aria-hidden="true">
    <circle cx="34" cy="34" r="34" fill="#e8231f"/>
    <rect x="22" y="18" width="24" height="32" rx="2" fill="#fff"/>
    <rect x="25" y="21" width="18" height="26" fill="#e8231f"/>
    <path d="M30 18 V33 L34 30 L38 33 V18 Z" fill="#fff"/>
  </svg>
  <h1 class="hero-title">• Club Forms •</h1>

  <main class="content">
    <div class="intro-band"></div>
    <div class="dots">•••</div>
    <div class="section-rule" style="left:0;width:294px"></div>
    <div class="section-rule" style="left:456px;width:294px"></div>
    <h2 class="section-title"><span>CLUB FORMS</span></h2>
    <p class="intro-text">It is important that if any occurrences or accident's arise during the season, It is vital that players fill out the appropriate forms for processing. Players must understand forms need to be filled in and handed to the club within 24hr of the incident. The forms can either be handed to a Tavenhurst FC Committee Member or emailed to the club at TavenhurstFC@fieldmail.net.Players, parents and spectators must understand code of conduct is important to the club. Failure to do so will result in disciplinary action by the club and further punishment by the association. The club has a zero tolerance to any incidences, whether it be a home or away game. All players and parents have filled out the code of conduct forms. It is vital you all abide by these rules.</p>

    <span class="form-btn red" style="left:30px;top:264px">Registration</span>
    <span class="form-btn black small" style="left:264px;top:264px">Code of Conduct Players Form</span>
    <span class="form-btn red small" style="left:498px;top:264px">Code of Conduct Parents Form</span>
    <span class="form-btn black" style="left:30px;top:341px">Certificate of Currency</span>
    <span class="form-btn red small" style="left:264px;top:341px">Personal Injury Insurance flyer</span>
    <span class="form-btn black small" style="left:498px;top:341px">Personal Accident Claim Form</span>
    <span class="form-btn red" style="left:30px;top:418px">Match Day Checklist</span>
    <span class="form-btn black small" style="left:264px;top:418px">Sports Programme Summary</span>

    <span class="badge black" style="left:205px;top:236px">01</span>
    <span class="badge red" style="left:439px;top:236px">02</span>
    <span class="badge black" style="left:673px;top:236px">03</span>
    <span class="badge red" style="left:205px;top:313px">04</span>
    <span class="badge black" style="left:439px;top:313px">05</span>
    <span class="badge red" style="left:673px;top:313px">06</span>
    <span class="badge black" style="left:205px;top:390px">07</span>
    <span class="badge red" style="left:439px;top:390px">08</span>
  </main>

  <div class="footer-rule"></div>
  <footer class="footer">
    <svg class="footer-icon" style="left:50px;top:25px" width="36" height="40" viewBox="0 0 36 40" aria-hidden="true">
      <path d="M8 3 H28 V14 C28 21 23 25 18 25 C13 25 8 21 8 14 Z" fill="#e7b512"/>
      <path d="M8 6 H3 C3 13 6 16 9 16 M28 6 H33 C33 13 30 16 27 16" fill="none" stroke="#e7b512" stroke-width="2.5"/>
      <rect x="15" y="25" width="6" height="7" fill="#c9960c"/>
      <rect x="10" y="32" width="16" height="5" rx="1" fill="#c9960c"/>
    </svg>
    <div class="footer-col" style="left:0">
      <h3 style="left:94px">Home</h3>
      <div class="underline" style="left:94px;width:75px"></div>
      <ul style="left:94px"><li>News</li><li>Gallery</li><li>Sponsor</li><li>Contact Us</li></ul>
    </div>

    <svg class="footer-icon" style="left:206px;top:28px" width="38" height="38" viewBox="0 0 38 38" aria-hidden="true">
      <circle cx="19" cy="19" r="17" fill="#fff" stroke="#111" stroke-width="2"/>
      <polygon points="19,12 25,17 23,24 15,24 13,17" fill="#111"/>
      <path d="M19 2 V12 M25 17 L35 14 M23 24 L29 33 M15 24 L9 33 M13 17 L3 14" stroke="#111" stroke-width="2"/>
    </svg>
    <div class="footer-col" style="left:0">
      <h3 style="left:252px">Club</h3>
      <div class="underline" style="left:252px;width:75px"></div>
      <ul style="left:252px"><li>History</li><li>Committee</li><li>Awards</li><li>Forms</li></ul>
    </div>

    <svg class="footer-icon" style="left:358px;top:28px" width="44" height="36" viewBox="0 0 44 36" aria-hidden="true">
      <polygon points="8,2 36,2 43,34 1,34" fill="#5bb53a"/>
      <polygon points="8,2 36,2 43,34 1,34" fill="none" stroke="#fff" stroke-width="1.5"/>
      <line x1="4.5" y1="18" x2="39.5" y2="18" stroke="#fff" stroke-width="1.5"/>
      <ellipse cx="22" cy="18" rx="6" ry="4" fill="none" stroke="#fff" stroke-width="1.5"/>
    </svg>
    <div class="footer-col" style="left:0">
      <h3 style="left:413px">Fixtures &amp; Results</h3>
      <div class="underline" style="left:413px;width:281px"></div>
      <ul style="left:413px">
        <li class="fixture-row"><span>Premier League</span><span>Under 10 / 2</span></li>
        <li class="fixture-row"><span>Premier League</span><span>Under 10 / 3</span></li>
        <li class="fixture-row"><span>ResSuper League</span><span>Under 11 / 1</span></li>
        <li class="fixture-row"><span>Super League Res</span><span>Under 12 / 3</span></li>
      </ul>
    </div>
  </footer>
  <div class="copyright">© 2012-2013 All Rights Reserved to Tavenhurst Falcons FC</div>
</div>
</body>
</html>
```